Veluxa Bone & Motion Business Card

Need a business card using the logo provided. I want brand side of the card to be grey with the logo in the center of the card in white.

On the other side I leave to the designers

Target Market(s)

Personal Injury Attorneys

Industry/Entity Type

Medical

Contact Information for Business Card

Name, CEO. Cell Phone, (Larkmoor, Address, Phone) (Fenwick, Address, Phone) (Ashbrook Bay, Address, Phone)

Colors

Designer to choose only greyscale colors for use in the design.

Requirements
Must have
• Logo by itself on one side

```html
<!DOCTYPE html>
<html lang="en">
<head>
<meta charset="utf-8">
<title>Veluxa Bone &amp; Motion — Business Card</title>
<link rel="stylesheet" href="https://fonts.googleapis.com/css2?family=Jost:wght@400;500;600&display=swap">
<style>
  :root {
    --backdrop: #c4dbe4;
    --card-white: #ffffff;
    --card-mist: #ececec;
    --band-grey: #9bb4ba;
    --accent-blue: #3f7bb9;
    --muted-teal: #8ba8ae;
    --ink: #4a4a4a;
    --icon-white: #ffffff;
  }
  * { box-sizing: border-box; margin: 0; padding: 0; }
  html, body { width: 1200px; height: 892px; overflow: hidden; }
  body {
    background: var(--backdrop);
    font-family: "Jost", "Futura", sans-serif;
    position: relative;
  }
  .card {
    position: absolute;
    top: 300px;
    width: 510px;
    height: 292px;
    overflow: hidden;
  }
  .card-texture {
    position: absolute; inset: 0;
    background: linear-gradient(160deg, var(--card-white) 30%, var(--card-mist) 100%);
  }
  /* Front side */
  .card-front { left: 50px; }
  .brand-band {
    position: absolute; left: 0; right: 0; top: 78px; height: 136px;
    background: var(--band-grey);
    border-top: 6px solid var(--accent-blue);
    border-bottom: 6px solid var(--accent-blue);
    display: flex; flex-direction: column; align-items: center; justify-content: center;
    color: var(--card-white);
    font-weight: 500;
    text-align: center;
  }
  .brand-name { font-size: 54px; letter-spacing: 10px; line-height: 1; padding-left: 10px; }
  .brand-tagline { font-size: 24px; letter-spacing: 6px; margin-top: 6px; padding-left: 6px; }
  /* Back side */
  .card-back { left: 640px; }
  .contact-side { position: absolute; left: 0; top: 0; width: 300px; height: 100%; }
  .mini-brand {
    position: absolute; left: 28px; top: 34px;
    color: var(--muted-teal); font-weight: 500; text-align: center;
  }
  .mini-brand .brand-name { font-size: 28px; letter-spacing: 5px; }
  .mini-brand .brand-tagline { font-size: 12px; letter-spacing: 3px; margin-top: 2px; }
  .person { position: absolute; left: 28px; bottom: 34px; }
  .person-name { font-size: 20px; font-weight: 600; color: var(--ink); }
  .person-role { font-size: 16px; color: var(--muted-teal); margin-top: 2px; }
  .person-cell { display: flex; align-items: center; gap: 10px; margin-top: 8px; font-size: 16px; color: var(--muted-teal); letter-spacing: 1px; }
  .locations-panel {
    position: absolute; left: 300px; top: 0; right: 0; bottom: 0;
    background: var(--band-grey);
    border-left: 6px solid var(--accent-blue);
    padding: 28px 0 0 40px;
  }
  .location { height: 82px; }
  .location-city { font-size: 14px; font-weight: 600; color: var(--accent-blue); }
  .location-icons { display: flex; flex-direction: column; gap: 8px; margin: 12px 0 0 10px; }
</style>
</head>
<body>

<section class="card card-front" aria-label="Brand side">
  <div class="card-texture" role="img" aria-label="Faint dot texture on white card stock"></div>
  <div class="brand-band">
    <div class="brand-name">VELUXA</div>
    <div class="brand-tagline">BONE &amp; MOTION</div>
  </div>
</section>

<section class="card card-back" aria-label="Contact side">
  <div class="card-texture" role="img" aria-label="Faint dot texture on white card stock"></div>
  <div class="contact-side">
    <div class="mini-brand">
      <div class="brand-name">VELUXA</div>
      <div class="brand-tagline">BONE &amp; MOTION</div>
    </div>
    <div class="person">
      <div class="person-name">Name</div>
      <div class="person-role">CEO</div>
      <div class="person-cell">
        <svg width="12" height="20" viewBox="0 0 12 20" aria-hidden="true"><rect x="1" y="1" width="10" height="18" rx="2" fill="none" stroke="var(--muted-teal)" stroke-width="1.6"/><line x1="4" y1="16" x2="8" y2="16" stroke="var(--muted-teal)" stroke-width="1.4"/></svg>
        <span>5550104477</span>
      </div>
    </div>
  </div>
  <div class="locations-panel">
    <div class="location">
      <div class="location-city">Larkmoor</div>
      <div class="location-icons">
        <svg width="14" height="14" viewBox="0 0 24 24" aria-hidden="true"><path fill="var(--icon-white)" d="M6.6 10.8a15 15 0 0 0 6.6 6.6l2.2-2.2a1 1 0 0 1 1-.25 11.4 11.4 0 0 0 3.6.6 1 1 0 0 1 1 1V20a1 1 0 0 1-1 1A17 17 0 0 1 3 4a1 1 0 0 1 1-1h3.5a1 1 0 0 1 1 1c0 1.25.2 2.45.6 3.6a1 1 0 0 1-.25 1z"/></svg>
        <svg width="12" height="16" viewBox="0 0 12 16" aria-hidden="true"><path fill="var(--icon-white)" d="M6 0a6 6 0 0 0-6 6c0 4.5 6 10 6 10s6-5.5 6-10a6 6 0 0 0-6-6zm0 8.2A2.2 2.2 0 1 1 6 3.8a2.2 2.2 0 0 1 0 4.4z"/></svg>
      </div>
    </div>
    <div class="location">
      <div class="location-city">Fenwick</div>
      <div class="location-icons">
        <svg width="14" height="14" viewBox="0 0 24 24" aria-hidden="true"><path fill="var(--icon-white)" d="M6.6 10.8a15 15 0 0 0 6.6 6.6l2.2-2.2a1 1 0 0 1 1-.25 11.4 11.4 0 0 0 3.6.6 1 1 0 0 1 1 1V20a1 1 0 0 1-1 1A17 17 0 0 1 3 4a1 1 0 0 1 1-1h3.5a1 1 0 0 1 1 1c0 1.25.2 2.45.6 3.6a1 1 0 0 1-.25 1z"/></svg>
        <svg width="12" height="16" viewBox="0 0 12 16" aria-hidden="true"><path fill="var(--icon-white)" d="M6 0a6 6 0 0 0-6 6c0 4.5 6 10 6 10s6-5.5 6-10a6 6 0 0 0-6-6zm0 8.2A2.2 2.2 0 1 1 6 3.8a2.2 2.2 0 0 1 0 4.4z"/></svg>
      </div>
    </div>
    <div class="location">
      <div class="location-city">Ashbrook Bay</div>
      <div class="location-icons">
        <svg width="14" height="14" viewBox="0 0 24 24" aria-hidden="true"><path fill="var(--icon-white)" d="M6.6 10.8a15 15 0 0 0 6.6 6.6l2.2-2.2a1 1 0 0 1 1-.25 11.4 11.4 0 0 0 3.6.6 1 1 0 0 1 1 1V20a1 1 0 0 1-1 1A17 17 0 0 1 3 4a1 1 0 0 1 1-1h3.5a1 1 0 0 1 1 1c0 1.25.2 2.45.6 3.6a1 1 0 0 1-.25 1z"/></svg>
        <svg width="12" height="16" viewBox="0 0 12 16" aria-hidden="true"><path fill="var(--icon-white)" d="M6 0a6 6 0 0 0-6 6c0 4.5 6 10 6 10s6-5.5 6-10a6 6 0 0 0-6-6zm0 8.2A2.2 2.2 0 1 1 6 3.8a2.2 2.2 0 0 1 0 4.4z"/></svg>
      </div>
    </div>
  </div>
</section>

</body>
</html>
```